A website where experts collaborate on your project

I am building a new website where experts (yes, like designers) collaborate on projects with the project owner. More minds = more collaboration = better end product. Please see Pelmora(dot)com for a quick landing page I created for collaborating on presentations (although there will be many project types offered)

I am looking for a DESIGNER LONG TERM, but for now, just need initial mock ups to show the web programmers.

I have 21 Word documents loosely designed, what I would like to see here is a theme. Please DO NOT GO OFF WHAT YOU CURRENTLY SEE AT PELMORA. What is up now is only a quick landing page.

You can view a Word doc of the homepage here:
https://www.filevanta.com/s/qx83kdm2/home.docx?dl=0

WHAT AM I LOOKING FOR?
A clean, well designed theme.

Here is a link to the logo:
https://www.filevanta.com/s/mr47tpz9/logo%20-%20horizontal.tif?dl=0
-----------------------------------------
Here are a few sites I like the design of and what I like about them:
www.quenbrook.com-all around my favorite, beautiful graphics, clean layout, bold use of colors on a dark background
Ravelto.com- clean layout, The use of humans and bubble style elements.
Mintharbor.com :) clean, bold, unique pop art style but professional
plumevault.com - From the unique colors and artwork and the ability of that art to not interfere with the important elements of the site
sparkwidgets.com-clean, nice colors, well organized and separated sections.
www.dunmereco.com-love the font, use of colors and sectionalized style

All in all, I am not picky and open to so many styles. I would ultimately like the designer I pick to design all 21 pages.
Updates

Hello everyone,Moving forward, I would like you all to pay special attention to the section in my brief titled "Here are a few sites I like the design of and what I like about them". Please see below, I handpicked each one of these as sites I really like. Thank you.Here are a few sites I like the design of and what I like about them:Ravelto.com- clean layout, The use of humans and bubble style elements.Mintharbor.com :) clean, bold, unique pop art style but professionalwriteraccess.com - From the unique colors and artwork and the ability of that art to not interfere with the important elements of the sitegrowthgeeks.com-clean, nice colors, well organized and separated sections.www.dunmereco.com-love the font, use of colors and sectionalized stylewww.quenbrook.com-beautiful graphics, clean layout, bold use of colors----------------------------------------- Added Tuesday, November 24, 2015

I updated the homepage, you can see it here:https://www.dropbox.com/s/kwlkbsookq3cg2m/1new%20homepage.docx?dl=0I am modeling it after my favorite designed site: triplelift.comI love the dark colors with the orange glowing style boldness of the buttons. It's real clean too. Added Tuesday, November 24, 2015

Target Market(s)

small business owners, marketers, freelancer writers, graphic designers,

Industry/Entity Type

Building

Number of Pages Required

5+ page

Requirements
Must have
• I can't think of anything the project must have.
Nice to have
• WHAT AM I LOOKING FOR?
• A clean, well designed theme. I had a designer do a bit of work putting elements together, I found it to be very plain, but I like the Application Page (https://www.filevanta.com/s/jb19ckr3/Pelmora-Website.ai?dl=0)
• Here is a link to the logo:
• https://www.filevanta.com/s/mr47tpz9/logo%20-%20horizontal.tif?dl=0
• Here are a few sites I like the design of and what I like about them:
• Ravelto.com- clean layout, The use of humans and bubble style elements.
• Mintharbor.com :) clean, bold, unique pop art style but professional
• plumevault.com - From the unique colors and artwork and the ability of that art to not interfere with the important elements of the site
• sparkwidgets.com-clean, nice colors, well organized and separated sections.
• www.dunmereco.com-love the font, use of colors and sectionalized style
• www.quenbrook.com-beautiful graphics, clean layout, bold use of colors
• -----------------------------------------
Should not have
• out of the boxed, templated style website. I want this site to be memorable and not look like a thousand others

```html
<!DOCTYPE html>
<html lang="en">
<head>
<meta charset="utf-8">
<title>Pelmora – Home</title>
<link href="https://fonts.googleapis.com/css2?family=Raleway:wght@400;500&family=Roboto:wght@300;400;700&family=Roboto+Condensed:wght@400;700&display=swap" rel="stylesheet">
<style>
:root{
  --orange:#f39a1e;
  --orange-dark:#e0861a;
  --blue:#3aa3d1;
  --teal:#5ab3c9;
  --text:#6f6f6f;
  --text-light:#9a9a9a;
  --panel:#f6f6f4;
  --line:#e6e6e3;
  --footer:#3b3b3b;
  --white:#fff;
}
*{box-sizing:border-box;margin:0;padding:0}
html,body{width:714px;height:1200px;overflow:hidden;background:var(--white)}
body{position:relative;font-family:'Roboto',sans-serif;color:var(--text)}
.abs{position:absolute}

/* header */
.site-header{position:absolute;left:0;top:0;width:714px;height:72px;background:var(--white)}
.brand{left:59px;top:24px;display:flex;align-items:center;gap:8px}
.brand-name{font-family:'Raleway',sans-serif;font-weight:500;font-size:19px;color:var(--orange);letter-spacing:.2px}
.brand-dot{width:14px;height:14px;border-radius:50%;background:var(--orange)}
.search{left:281px;top:26px;width:116px;height:22px;border:1px solid var(--orange);border-radius:2px;font-size:7px;color:var(--orange);padding:6px 7px;font-weight:700}
.search svg{position:absolute;right:7px;top:8px}
.nav{top:32px;font-size:7.5px;color:var(--text-light)}
.badge{left:639px;top:30px;width:17px;height:11px;background:var(--blue);color:#fff;font-size:6.5px;text-align:center;line-height:11px}
.badge::after{content:"";position:absolute;left:4px;bottom:-3px;border-left:3px solid var(--blue);border-bottom:3px solid transparent}

/* hero */
.hero{left:0;top:72px;width:714px;height:306px;background:linear-gradient(100deg,#6b6560 0%,#4a4440 40%,#2f2a27 70%,#3a3430 100%)}
.hero h1{position:absolute;left:84px;top:74px;font-family:'Raleway',sans-serif;font-weight:400;font-size:27px;color:#fff}
.hero p{position:absolute;left:88px;top:116px;font-family:'Roboto',sans-serif;font-weight:300;font-size:17px;line-height:23px;color:#fff}
.btn-start{position:absolute;left:87px;top:193px;width:132px;height:33px;background:var(--orange);color:#fff;font-weight:300;font-size:14px;text-align:center;line-height:33px}
.hero-arrow{position:absolute;top:148px;width:22px;height:22px;border:1px solid rgba(255,255,255,.8);border-radius:50%}

/* filters */
.filters{left:59px;top:437px;width:213px;height:494px;background:var(--panel)}
.filters-head{height:36px;background:var(--orange);color:#fff;font-family:'Raleway',sans-serif;font-size:15px;padding:9px 21px}
.f-row{position:absolute;left:20px;font-size:9px;color:var(--text)}
.f-sep{position:absolute;left:4px;width:205px;height:1px;background:var(--line)}
.plus{position:absolute;right:17px;width:7px;height:7px;border:1px solid #aaa}
.plus::before{content:"";position:absolute;left:1px;top:2px;width:3px;height:1px;background:#aaa}
.plus::after{content:"";position:absolute;left:2px;top:1px;width:1px;height:3px;background:#aaa}
.country-item{position:absolute;left:24px;font-size:7.5px;color:var(--text-light)}
.country-item i{display:inline-block;width:5px;height:5px;background:var(--orange);margin-right:16px;vertical-align:middle}
.save-btn{left:90px;top:916px;width:147px;height:29px;background:var(--teal);color:#fff;font-size:14px;text-align:center;line-height:29px}

/* projects */
.section-title{font-family:'Raleway',sans-serif;font-size:16px;color:var(--orange)}
.sort{font-size:8px;color:var(--text)}
.sort .on{color:var(--blue)}
.proj-box{left:321px;width:334px;background:var(--panel)}
.proj{position:absolute;left:20px}
.proj .thumb{position:absolute;left:0;top:0;width:80px;height:51px}
.proj p{position:absolute;left:99px;top:4px;width:210px;font-size:9.6px;line-height:19px;color:var(--text)}
.proj b{color:#444}
.proj-sep{position:absolute;left:6px;width:322px;height:1px;background:var(--line)}

/* testimonial */
.testimonial{left:0;top:1004px;width:714px;height:142px;background:linear-gradient(90deg,#2c5461 0%,#3b6f77 50%,#2f5e6b 100%)}
.avatar{position:absolute;left:91px;top:22px;width:104px;height:104px;border-radius:50%;background:#fff}
.avatar .photo{position:absolute;left:9px;top:9px;width:86px;height:86px;border-radius:50%;background:radial-gradient(circle at 50% 45%,#b58a6a,#5b3f2e)}
.bubble-tail{position:absolute;left:150px;top:108px}
.quote{position:absolute;left:243px;top:39px;font-family:'Roboto Condensed',sans-serif;font-size:13.6px;line-height:18.5px;color:#fff}
.quote-author{position:absolute;left:243px;top:86px;font-family:'Roboto Condensed',sans-serif;font-weight:700;font-size:14.5px;color:#fff}
.quote-author span{color:var(--orange)}
.t-arrow{position:absolute;top:69px;width:18px;height:18px;border:2px solid #1e2f33;border-radius:50%}

/* footer */
.site-footer{left:0;top:1146px;width:714px;height:54px;background:var(--footer)}
.site-footer .copy{position:absolute;left:59px;top:22px;font-size:8px;color:#ddd}
.social{position:absolute;top:17px;width:19px;height:19px}
</style>
</head>
<body>

<header class="site-header">
  <div class="abs brand"><span class="brand-name">pelmora</span><span class="brand-dot"></span></div>
  <div class="abs search">Search
    <svg width="6" height="4" viewBox="0 0 6 4"><path d="M0 0h6L3 4z" fill="#f39a1e"/></svg>
  </div>
  <span class="abs nav" style="left:420px">Projects</span>
  <span class="abs nav" style="left:466px">How it works</span>
  <span class="abs nav" style="left:536px">Plans</span>
  <span class="abs nav" style="left:578px">My Account</span>
  <span class="abs badge">14</span>
</header>

<section class="abs hero" role="img" aria-label="Photo of a person typing on a laptop at an office desk">
  <h1>Convert More Customers</h1>
  <p>Experience the power of experts collaborating<br>on your project.</p>
  <div class="btn-start">Get Started</div>
  <svg class="hero-arrow" style="left:25px" viewBox="0 0 22 22"><path d="M12.5 7l-4 4 4 4" stroke="#fff" fill="none"/></svg>
  <svg class="hero-arrow" style="left:665px" viewBox="0 0 22 22"><path d="M9.5 7l4 4-4 4" stroke="#fff" fill="none"/></svg>
</section>

<aside class="abs filters">
  <div class="filters-head">Filters</div>
  <span class="f-row" style="top:58px">Price</span>
  <svg class="abs" style="left:50px;top:46px" width="160" height="28" viewBox="0 0 160 28">
    <text x="2" y="22" font-size="6" fill="#3aa3d1" font-family="Roboto">$20</text>
    <line x1="20" y1="20" x2="125" y2="20" stroke="#444" stroke-width="1"/>
    <text x="131" y="22" font-size="6" fill="#3aa3d1" font-family="Roboto">$1000</text>
    <rect x="34" y="3" width="12" height="8" fill="#fff" stroke="#bbb" stroke-width=".5"/>
    <text x="36.5" y="9" font-size="5" fill="#777" font-family="Roboto">50</text>
    <circle cx="40" cy="20" r="4" fill="#b9dcec" stroke="#3aa3d1"/>
  </svg>
  <div class="f-sep" style="top:87px"></div>
  <span class="f-row" style="top:100px;color:var(--blue)">Country</span>
  <svg class="abs" style="left:189px;top:101px" width="8" height="8"><rect x=".5" y=".5" width="7" height="7" fill="none" stroke="#3aa3d1"/><path d="M2 4h4" stroke="#3aa3d1"/></svg>
  <span class="country-item" style="top:125px;color:var(--blue)"><i style="background:#7cab7e"></i>Afghanistan</span>
  <span class="country-item" style="top:148px"><i></i>Albania</span>
  <span class="country-item" style="top:171px"><i></i>Algeria</span>
  <span class="country-item" style="top:193px"><i></i>American Samoa</span>
  <span class="country-item" style="top:216px"><i></i>Andorra</span>
  <div class="f-sep" style="top:239px"></div>
  <span class="f-row" style="top:251px">Categories</span><span class="plus" style="top:253px"></span>
  <div class="f-sep" style="top:275px"></div>
  <span class="f-row" style="top:286px;left:19px">Time Left</span><span class="plus" style="top:288px"></span>
  <span class="country-item" style="top:321px;font-size:9px;color:var(--text)"><i style="background:#7cab7e;margin-right:13px"></i>Active</span>
  <span class="country-item" style="top:321px;left:120px;font-size:9px;color:var(--text)"><i style="margin-right:16px"></i>Expired</span>
  <div class="f-sep" style="top:344px"></div>
  <span class="f-row" style="top:356px;left:19px">Contains adult content</span><span class="plus" style="top:358px"></span>
  <div class="f-sep" style="top:380px"></div>
  <span class="f-row" style="top:393px">Keywords</span><span class="plus" style="top:394px"></span>
  <div class="f-sep" style="top:416px"></div>
  <span class="f-row" style="top:429px">Followers</span><span class="plus" style="top:430px"></span>
</aside>
<div class="abs save-btn">Save filter</div>

<h2 class="abs section-title" style="left:321px;top:447px">Crowd Projects:</h2>
<div class="abs sort" style="left:505px;top:452px">Sort :&nbsp;&nbsp; <span class="on">Price</span><span style="margin-left:19px">Country</span><span style="margin-left:19px">Time left</span></div>
<div class="abs proj-box" style="top:480px;height:156px">
  <div class="proj" style="top:14px">
    <div class="thumb" role="img" aria-label="Photo of two businessmen meeting at a laptop" style="background:linear-gradient(135deg,#c9d7e6,#5c6f88)"></div>
    <p>Morbi in ante arcu. Maecenas sit amet sem vel <b>.$80</b>, U.K., time left: 6 days</p>
  </div>
  <div class="proj-sep" style="top:76px"></div>
  <div class="proj" style="top:90px">
    <div class="thumb" role="img" aria-label="Photo of a businessman in front of a glass building" style="background:linear-gradient(135deg,#8fb4dc,#3f5f8c)"></div>
    <p>Lorem ipsum dolor sit amet, consectetur adipiscing <b>$90</b>, CA., time left: 6 days</p>
  </div>
</div>
<svg class="abs" style="left:328px;top:658px" width="327" height="2"><line x1="0" y1="1" x2="327" y2="1" stroke="#e3e3e0" stroke-dasharray="2 2"/></svg>

<h2 class="abs section-title" style="left:321px;top:682px">Featured Projects:</h2>
<div class="abs sort" style="left:505px;top:687px">Sort :&nbsp;&nbsp; <span class="on">Price</span><span style="margin-left:19px">Country</span><span style="margin-left:19px">Time left</span></div>
<div class="abs proj-box" style="top:717px;height:235px">
  <div class="proj" style="top:15px">
    <div class="thumb" role="img" aria-label="Photo of a team of colleagues at a table" style="background:linear-gradient(135deg,#eef0f3,#6d7a8c)"></div>
    <p>Neque porro quisquam est qui dolorem ipsum <b>$250</b>, U.S., time left: 6 days</p>
  </div>
  <div class="proj-sep" style="top:78px"></div>
  <div class="proj" style="top:91px">
    <div class="thumb" role="img" aria-label="Photo of a man working at a computer" style="background:linear-gradient(135deg,#9aa3ae,#3e4a5a)"></div>
    <p>Duis ligula sapien, sodales id tortor vitae, ornare <b>$62</b>, U.K., time left: 6 days</p>
  </div>
  <div class="proj-sep" style="top:153px"></div>
  <div class="proj" style="top:167px">
    <div class="thumb" role="img" aria-label="Photo of two businessmen reviewing documents" style="background:linear-gradient(135deg,#3f4f8a,#1f2433)"></div>
    <p>Neque porro quisquam est qui dolorem &nbsp;ipsum<b>$250</b>, U.S., time left: 6 days</p>
  </div>
</div>

<section class="abs testimonial" role="img" aria-label="Background mosaic of small portrait photos in teal tones">
  <svg class="t-arrow" style="left:44px" viewBox="0 0 18 18"><path d="M10 5L6 9l4 4z" fill="#1e2f33"/></svg>
  <svg class="bubble-tail" width="58" height="20" viewBox="0 0 58 20"><path d="M0 0L58 20H10z" fill="#fff"/></svg>
  <div class="avatar"><div class="photo" role="img" aria-label="Portrait photo of the quoted customer"></div></div>
  <p class="quote">“With Pelmora I have multiple experts perfecting my content<br>and I only pay for the feedback I find valuable. It’s perfect”</p>
  <p class="quote-author">- Dale Marsh, <span>CEO</span></p>
  <svg class="t-arrow" style="left:662px" viewBox="0 0 18 18"><path d="M8 5l4 4-4 4z" fill="#1e2f33"/></svg>
</section>

<footer class="abs site-footer">
  <span class="copy">Copyrights@pelmora 2015</span>
  <span class="social" style="left:494px;background:#3b5a9a"></span>
  <span class="social" style="left:523px;background:#cb2027"></span>
  <span class="social" style="left:552px;background:#2aa3e0"></span>
  <span class="social" style="left:581px;background:#d6492f"></span>
  <span class="social" style="left:609px;background:#f08a1d"></span>
</footer>

</body>
</html>
```